Business Card Design for Occupational Medicine Start Up Company

We need to design a professional business card. We are a healthcare company providing occupational medicine services to blue collar industries. We are professional, efficient and high quality service providers.

Target Market(s)

Blue Collar Industry: Shipbuilding, Ports, Trucking Companies; The Executives and Safety Officers for these companies

Industry/Entity Type

Healthcare

Contact Information for Business Card

Logo, Name, Title, Email, Phone

Other font styles liked:
• Please match our Brand Guide

Requirements
Must have
• Our Company Colors and Logo

```html
<!DOCTYPE html>
<html lang="en">
<head>
<meta charset="utf-8">
<title>Harborline Clinics – Business Card</title>
<link href="https://fonts.googleapis.com/css2?family=Montserrat:wght@400;600;700&display=swap" rel="stylesheet">
<style>
  :root {
    --navy: #29337a;
    --sky: #23a4df;
    --amber: #f0b04f;
    --mist: #e6e6e6;
    --paper: #ffffff;
    --ink: #3a3a3a;
    --page: #e5e5e5;
  }
  * { margin: 0; padding: 0; box-sizing: border-box; }
  html, body { width: 1018px; height: 1200px; overflow: hidden; }
  body {
    background: var(--page);
    font-family: "Montserrat", Arial, sans-serif;
    position: relative;
  }
  .brand-lockup {
    position: absolute;
    top: 300px; left: 0; width: 1018px;
    display: flex; align-items: center; justify-content: center; gap: 16px;
  }
  .brand-dot { width: 62px; height: 62px; border-radius: 50%; background: var(--sky); }
  .brand-name {
    font-weight: 700; color: var(--navy);
    font-size: 30px; letter-spacing: 0.5px; line-height: 1;
  }
  .card {
    position: absolute;
    top: 520px;
    width: 428px; height: 245px;
    overflow: hidden;
  }
  .card-front { left: 61px; background: var(--paper); }
  .card-back { left: 528px; background: var(--navy); }

  .shape { position: absolute; border-radius: 50%; }
  .shape-navy { width: 234px; height: 234px; left: 289px; top: -87px; background: var(--navy); }
  .shape-mist { width: 90px; height: 90px; left: 241px; top: 118px; background: var(--mist); }
  .shape-amber { width: 70px; height: 70px; left: 350px; top: 166px; background: var(--amber); }
  .shape-sky { width: 86px; height: 86px; left: -18px; top: 218px; background: var(--sky); }

  .front-brand {
    position: absolute; left: 20px; top: 36px;
    display: flex; align-items: center; gap: 8px;
  }
  .front-brand .brand-dot { width: 30px; height: 30px; }
  .front-brand .brand-name { font-size: 13px; }

  .person { position: absolute; left: 42px; top: 121px; }
  .person-name {
    font-weight: 700; color: var(--sky);
    font-size: 15px; letter-spacing: -0.2px; line-height: 1.1;
  }
  .person-title {
    font-weight: 400; color: var(--ink);
    font-size: 11.5px; letter-spacing: 0.4px; margin-top: 2px;
  }
  .contacts { position: absolute; left: 42px; top: 163px; list-style: none; }
  .contacts li {
    display: flex; align-items: center; gap: 5px;
    font-size: 7.6px; color: var(--ink); height: 11.6px; letter-spacing: 0.2px;
  }
  .contacts svg { width: 7px; height: 7px; flex: none; }

  .back-brand {
    position: absolute; inset: 0;
    display: flex; flex-direction: column; align-items: center; justify-content: center; gap: 12px;
  }
  .back-brand .brand-dot { width: 52px; height: 52px; }
  .back-brand .brand-name { color: var(--paper); font-size: 15px; }
</style>
</head>
<body>
  <header class="brand-lockup">
    <span class="brand-dot"></span>
    <span class="brand-name">HARBORLINE CLINICS</span>
  </header>

  <section class="card card-front">
    <span class="shape shape-navy"></span>
    <span class="shape shape-mist"></span>
    <span class="shape shape-amber"></span>
    <span class="shape shape-sky"></span>

    <div class="front-brand">
      <span class="brand-dot"></span>
      <span class="brand-name">HARBORLINE CLINICS</span>
    </div>

    <div class="person">
      <p class="person-name">DANIEL R. MOREAU</p>
      <p class="person-title">Chief Executive Manager</p>
    </div>

    <ul class="contacts">
      <li>
        <svg viewBox="0 0 10 10"><rect width="10" height="10" fill="#f0b04f"/><path d="M3 2.5l1.2 1.3-.6.8c.5 1 1.1 1.6 2 2l.8-.6L7.6 7.3 6.8 8C4.5 7.6 2.6 5.6 2.2 3.3z" fill="#fff"/></svg>
        +1 555-010-2040
      </li>
      <li>
        <svg viewBox="0 0 10 10"><rect width="10" height="10" fill="#f0b04f"/><rect x="2" y="3" width="6" height="4.2" fill="none" stroke="#fff" stroke-width=".9"/><path d="M2 3l3 2.3L8 3" fill="none" stroke="#fff" stroke-width=".9"/></svg>
        info@harborline.com
      </li>
      <li>
        <svg viewBox="0 0 10 10"><rect width="10" height="10" fill="#f0b04f"/><circle cx="5" cy="5" r="2.6" fill="none" stroke="#fff" stroke-width=".9"/><path d="M2.4 5h5.2M5 2.4c-1.2 1.5-1.2 3.7 0 5.2M5 2.4c1.2 1.5 1.2 3.7 0 5.2" fill="none" stroke="#fff" stroke-width=".6"/></svg>
        harborline.com
      </li>
      <li>
        <svg viewBox="0 0 10 10"><rect width="10" height="10" fill="#f0b04f"/><path d="M5 8.2C3.4 6.4 2.7 5.2 2.7 4.1a2.3 2.3 0 0 1 4.6 0c0 1.1-.7 2.3-2.3 4.1z" fill="#fff"/><circle cx="5" cy="4.1" r=".9" fill="#f0b04f"/></svg>
        88 Dockside Way Portsmouth, VA 23704
      </li>
    </ul>
  </section>

  <section class="card card-back">
    <div class="back-brand">
      <span class="brand-dot"></span>
      <span class="brand-name">HARBORLINE CLINICS</span>
    </div>
  </section>
</body>
</html>
```